Stonebridge Building and Projects business cards

A business card with watermark background (construction work)

Company logo attached

Home improvement projects
House renovations
Bathroom and kitchen renovations
House extensions
New builds and granny flats

Director Omar Haddani
(Phone number)
omar@sbpbuilding.com.au
(Instagram logo) sbp_building

```html
<!DOCTYPE html>
<html lang="en">
<head>
<meta charset="utf-8">
<title>Stonebridge Building and Projects – Business Cards</title>
<link rel="stylesheet" href="https://fonts.googleapis.com/css2?family=Raleway:wght@500;700;800&family=Arimo:wght@400&display=swap">
<style>
  :root {
    --brand-blue: #2f78b8;
    --ink-dark: #444444;
    --ink-text: #222222;
    --paper: #ffffff;
    --backdrop: #e9eaec;
  }
  * { box-sizing: border-box; margin: 0; padding: 0; }
  html, body { width: 1200px; height: 900px; overflow: hidden; }
  body {
    background: var(--backdrop);
    display: flex;
    flex-direction: column;
    align-items: center;
    justify-content: center;
    gap: 36px;
    font-family: "Arimo", Arial, sans-serif;
  }
  .card {
    position: relative;
    width: 700px;
    height: 400px;
    overflow: hidden;
    box-shadow: 0 6px 18px rgba(0,0,0,0.18);
  }

  /* Back of card */
  .card-back {
    background: var(--brand-blue);
    color: var(--paper);
    display: flex;
    flex-direction: column;
    align-items: center;
    justify-content: center;
    text-align: center;
  }
  .wordmark {
    display: flex;
    align-items: center;
    gap: 12px;
    font-family: "Raleway", Arial, sans-serif;
    font-weight: 800;
  }
  .wordmark-square {
    width: 18px;
    height: 18px;
    background: currentColor;
    flex: none;
  }
  .card-back .wordmark { font-size: 34px; line-height: 1.1; margin-bottom: 56px; }
  .wordmark-text { display: block; text-align: left; }
  .services {
    list-style: none;
    font-size: 17px;
    line-height: 1.45;
    letter-spacing: 0.3px;
  }

  /* Front of card */
  .card-front { background: var(--paper); }
  .holder {
    position: absolute;
    left: 46px;
    top: 58px;
  }
  .holder-name {
    font-family: "Raleway", Arial, sans-serif;
    font-weight: 800;
    font-size: 30px;
    color: var(--brand-blue);
  }
  .holder-role { font-size: 17px; color: var(--ink-text); margin-top: 2px; }
  .card-front .wordmark {
    position: absolute;
    right: 36px;
    top: 52px;
    color: var(--brand-blue);
    font-size: 24px;
    line-height: 1.15;
  }
  .contact-list {
    position: absolute;
    left: 46px;
    top: 212px;
    list-style: none;
    font-size: 17px;
    color: var(--ink-text);
    line-height: 1.55;
  }
  .contact-item { display: flex; align-items: center; gap: 10px; }
  .contact-icon { width: 17px; height: 17px; flex: none; }
  .swoosh { position: absolute; inset: 0; width: 700px; height: 400px; }
  .social-handle {
    position: absolute;
    right: 34px;
    top: 250px;
    display: flex;
    align-items: center;
    gap: 10px;
    color: var(--paper);
    font-size: 17px;
  }
  .social-square { width: 16px; height: 16px; background: var(--paper); border-radius: 3px; }
</style>
</head>
<body>

  <section class="card card-back" aria-label="Business card back">
    <div class="wordmark">
      <span class="wordmark-square"></span>
      <span class="wordmark-text">Stonebridge Building<br>and Projects</span>
    </div>
    <ul class="services">
      <li>Home improvement projects &nbsp;| House renovations</li>
      <li>Bathroom and kitchen renovations</li>
      <li>House extensions | &nbsp;New builds and granny flats</li>
    </ul>
  </section>

  <section class="card card-front" aria-label="Business card front">
    <svg class="swoosh" viewBox="0 0 700 400" aria-hidden="true">
      <path d="M0 318 C 150 322, 290 300, 420 250 C 470 232, 500 218, 520 212 C 450 262, 330 320, 180 335 C 100 342, 40 340, 0 340 Z" fill="var(--ink-dark)"/>
      <path d="M0 346 C 160 346, 320 320, 470 252 C 560 212, 630 196, 700 190 L700 400 L0 400 Z" fill="var(--brand-blue)"/>
    </svg>

    <div class="holder">
      <h1 class="holder-name">Omar Haddani</h1>
      <p class="holder-role">Director</p>
    </div>

    <div class="wordmark">
      <span class="wordmark-square"></span>
      <span class="wordmark-text">Stonebridge Building<br>and Projects</span>
    </div>

    <ul class="contact-list">
      <li class="contact-item">
        <svg class="contact-icon" viewBox="0 0 24 24" aria-hidden="true"><path d="M6.6 10.8a15 15 0 0 0 6.6 6.6l2.2-2.2a1 1 0 0 1 1-.25 11.4 11.4 0 0 0 3.6.57 1 1 0 0 1 1 1V20a1 1 0 0 1-1 1A17 17 0 0 1 3 4a1 1 0 0 1 1-1h3.5a1 1 0 0 1 1 1c0 1.25.2 2.45.57 3.57a1 1 0 0 1-.25 1z" fill="var(--brand-blue)"/></svg>
        044-987 650 321
      </li>
      <li class="contact-item">
        <svg class="contact-icon" viewBox="0 0 24 24" aria-hidden="true"><rect x="2" y="5" width="20" height="14" fill="var(--brand-blue)"/><path d="M2 5l10 8 10-8" fill="none" stroke="var(--paper)" stroke-width="1.6"/></svg>
        omar@sbpbuilding.com.au
      </li>
      <li class="contact-item">
        <svg class="contact-icon" viewBox="0 0 24 24" aria-hidden="true"><circle cx="12" cy="12" r="10" fill="none" stroke="var(--brand-blue)" stroke-width="2"/><ellipse cx="12" cy="12" rx="4" ry="10" fill="none" stroke="var(--brand-blue)" stroke-width="1.6"/><path d="M2 12h20M4 7h16M4 17h16" stroke="var(--brand-blue)" stroke-width="1.4"/></svg>
        www.sbpbuilding.com.au
      </li>
    </ul>

    <div class="social-handle">
      <span class="social-square"></span>
      sbp_building
    </div>
  </section>

</body>
</html>
```